Web Design

We need a website for a company based in Doha Qatar called
Lumara Maid Service.

It is the number one maid cleaning service company, and we have branches all over qatar.

Luxury Cleaning Service Provider.

The color scheme is gold, yellow and black like the logo.

Before they get to the website, there is an intro video.

The website should depict luxury.

Target Market(s)

People who need maids at their houses.

Industry/Entity Type

Cleaning Service

Requirements
Must have
• Luxury, Sleek, Modern

The opening sequence is a video which I already have. Its too big to upload here so I am going to put it on youtube.

After the opening sequence, the home page should have a widescreen photo background and it should change every five seconds, the first background photo should be of qatar westbay skyline. Then the second background should be of maid photos in cleaning positions. Then the third background should be of cleaner photos etc.

We will send you all the tabs and all the content later.

```html
<!DOCTYPE html>
<html lang="en">
<head>
<meta charset="utf-8">
<title>Lumara Maid Service</title>
<link rel="stylesheet" href="https://fonts.googleapis.com/css2?family=Open+Sans:wght@300;400&family=Arimo:wght@700&display=swap">
<style>
  :root {
    --night: #0d1426;
    --night-mid: #1c2a4d;
    --night-glow: #3a4a7a;
    --gold: #c9a54a;
    --yellow: #fff57e;
    --white: #ffffff;
    --nav: #f2f2f2;
    --nav-active: #b9bcc6;
    --black: #000000;
    --footer-text: #7b7b7b;
  }
  * { margin: 0; padding: 0; box-sizing: border-box; }
  html, body { width: 1200px; height: 657px; overflow: hidden; background: var(--black); }
  .page { position: relative; width: 1200px; height: 657px; font-family: "Open Sans", sans-serif; }

  .hero-backdrop {
    position: absolute; left: 0; top: 0; width: 1200px; height: 592px;
    background:
      radial-gradient(ellipse 60% 45% at 55% 42%, var(--night-glow) 0%, transparent 70%),
      linear-gradient(180deg, var(--night) 0%, var(--night-mid) 55%, #2b3a63 72%, #1a2440 86%, #243156 100%);
  }

  .brand { position: absolute; left: 171px; top: 56px; display: flex; align-items: center; gap: 10px; }
  .brand-dot { width: 22px; height: 22px; border-radius: 50%; background: var(--gold); }
  .brand-name { font-family: "Open Sans", sans-serif; font-weight: 400; font-size: 21px; color: var(--gold); letter-spacing: 0.5px; }

  .main-nav { position: absolute; top: 67px; left: 444px; }
  .main-nav a {
    position: absolute; white-space: nowrap; text-decoration: none;
    font-family: "Arimo", sans-serif; font-weight: 700; font-size: 12px; color: var(--nav);
  }
  .main-nav a.is-active { color: var(--nav-active); }

  .slide-arrow { position: absolute; top: 284px; width: 18px; height: 48px; }
  .slide-arrow.prev { left: 76px; }
  .slide-arrow.next { left: 1104px; }

  .hero-title {
    position: absolute; left: 0; width: 1200px; top: 232px; text-align: center;
    font-weight: 300; font-size: 52px; color: var(--yellow); line-height: 1.2;
  }
  .hero-lead {
    position: absolute; left: 230px; width: 740px; top: 302px; text-align: center;
    font-weight: 300; font-size: 27px; color: var(--white); line-height: 40px;
  }
  .video-button {
    position: absolute; left: 418px; top: 397px; width: 340px; height: 68px;
    background: var(--black); display: flex; align-items: center; padding-left: 29px; gap: 11px;
    text-decoration: none;
  }
  .video-button span { font-weight: 300; font-size: 25px; color: var(--white); }

  .site-footer { position: absolute; left: 0; top: 592px; width: 1200px; height: 65px; background: var(--black); }
  .site-footer .note, .site-footer a {
    position: absolute; top: 24px; font-size: 11px; color: var(--footer-text); text-decoration: none; white-space: nowrap;
  }
  .social-dot { position: absolute; top: 30px; width: 9px; height: 9px; border-radius: 50%; background: var(--footer-text); }
</style>
</head>
<body>
<div class="page">
  <div class="hero-backdrop" role="img" aria-label="Night skyline of West Bay, Doha, with lit towers reflected in the water"></div>

  <header>
    <div class="brand">
      <span class="brand-dot"></span>
      <span class="brand-name">Lumara Maid Service</span>
    </div>
    <nav class="main-nav">
      <a class="is-active" style="left:0">ABOUT US</a>
      <a style="left:120px">SERVICES</a>
      <a style="left:240px">TESTIMONIALS</a>
      <a style="left:387px">VIDEOS</a>
      <a style="left:492px">CONTACT US</a>
    </nav>
  </header>

  <svg class="slide-arrow prev" viewBox="0 0 18 48" aria-label="Previous slide"><polyline points="16,1 2,24 16,47" fill="none" stroke="#c8ccd8" stroke-width="1.5"/></svg>
  <svg class="slide-arrow next" viewBox="0 0 18 48" aria-label="Next slide"><polyline points="2,1 16,24 2,47" fill="none" stroke="#c8ccd8" stroke-width="1.5"/></svg>

  <h1 class="hero-title">Lumara Maid Service</h1>
  <p class="hero-lead">We are a very famous cleaning company in Qatar and have branches all over.</p>
  <a class="video-button" href="#videos">
    <svg width="46" height="46" viewBox="0 0 46 46" aria-hidden="true">
      <circle cx="23" cy="23" r="21" fill="none" stroke="#fff" stroke-width="2.5"/>
      <polygon points="16,10 35,23 16,36 20,23" fill="#fff"/>
    </svg>
    <span>Click here for Videos</span>
  </a>

  <footer class="site-footer">
    <span class="note" style="left:173px">© Lumara Maid Service. 2014</span>
    <a style="left:327px" href="#privacy">Privacy Policy</a>
    <a style="left:417px" href="#terms">Terms</a>
    <span class="note" style="left:860px">Follow Us :</span>
    <span class="social-dot" style="left:917px"></span>
    <span class="social-dot" style="left:952px"></span>
    <span class="social-dot" style="left:988px"></span>
    <span class="social-dot" style="left:1018px"></span>
  </footer>
</div>
</body>
</html>
```